Geschäftspapiere für Handwerksunternehmen
Zielgruppe
Handwerk
Elektroinstallation
Design Modern
Aufgabenstellung
Anschrift, Kontaktdaten, Bankverbindung, Logo,
Im Haselgrund 9 88682 Salem Inhaber Lenno Brüchert
Telefon: 07412-6640285 Email: info@rvb-stromtechnik.de Internet: www.rvb-stromtechnik.de
Finanzamt Dornhalden USt.-ID: DE574016328 Steuer Nr.:4190357762
Kreisbank Talgau IBAN:DE71480392610007315946 BIC:KRTAGES1XYZ

```html
<!DOCTYPE html>
<html lang="de">
<head>
<meta charset="utf-8">
<title>RVB Stromtechnik – Geschäftspapiere</title>
<link rel="stylesheet" href="https://fonts.googleapis.com/css2?family=Montserrat:wght@400;600;700&display=swap">
<style>
  :root{
    --bg:#e1e2e6;
    --paper:#f4f5f7;
    --white:#ffffff;
    --ink:#0b0b0b;
    --yellow:#f2e928;
    --faint:#f6f3cf;
    --text:#2a2a2a;
    --muted:#555555;
  }
  *{margin:0;padding:0;box-sizing:border-box}
  html,body{width:1200px;height:936px;overflow:hidden;background:var(--bg);font-family:"Montserrat",sans-serif;color:var(--text)}
  .canvas{position:relative;width:1200px;height:936px}
  .piece{position:absolute;overflow:hidden}
  .brand{font-family:"Montserrat",sans-serif;font-weight:700;color:var(--yellow);white-space:nowrap;display:flex;align-items:center;gap:.35em;letter-spacing:.04em}
  .brand .dot{width:.8em;height:.8em;border-radius:50%;background:var(--yellow);flex:none}
  .brand--dark{color:var(--ink)}

  /* Visitenkarte Vorderseite */
  .card-front{left:154px;top:239px;width:179px;height:105px;background:var(--white)}
  .card-front .brand{position:absolute;left:13px;top:20px;font-size:13px}
  .card-front .name{position:absolute;left:12px;top:70px;font-size:5px;font-weight:700;color:var(--ink)}
  .card-front .name span{color:var(--yellow)}
  .card-front .rule{position:absolute;left:66px;top:73px;width:100px;height:1px;background:var(--ink)}
  .card-front .role{position:absolute;left:12px;top:76px;font-size:4px;font-weight:600}
  .card-front .contact{position:absolute;left:12px;top:84px;font-size:4.2px;line-height:6px;font-weight:600}
  .card-front .contact i{display:inline-block;width:3px;height:3px;background:var(--yellow);border-radius:50%;margin-right:3px}
  .card-front .web{position:absolute;right:10px;top:90px;font-size:4.2px;font-weight:600}

  /* Visitenkarte Rückseite */
  .card-back{left:150px;top:399px;width:180px;height:103px;background:var(--ink);display:flex;align-items:center;justify-content:center}
  .card-back .brand{font-size:12px}

  /* Briefbogen */
  .letterhead{left:396px;top:230px;width:317px;height:448px;background:var(--paper)}
  .letterhead .brand{position:absolute;left:31px;top:43px;font-size:17px}
  .letterhead .address{position:absolute;left:31px;top:73px;font-size:5px;line-height:8.5px;font-weight:600;color:var(--muted)}
  .letterhead .rule{position:absolute;left:31px;top:91px;width:82px;height:1px;background:var(--yellow)}
  .letterhead .mail{position:absolute;left:31px;top:94px;font-size:5px;line-height:8px;font-weight:600;color:var(--muted)}
  .letterhead .deco{position:absolute;left:130px;top:100px}
  .letterhead .footer{position:absolute;left:0;top:404px;width:317px;height:44px}
  .letterhead .footer svg{position:absolute;left:0;top:0}
  .letterhead .offices{position:absolute;left:10px;top:5px;font-size:4.4px;line-height:7.6px;font-weight:600;color:var(--white);white-space:nowrap}
  .letterhead .bank{position:absolute;left:100px;top:5px;font-size:4.4px;line-height:7.6px;font-weight:600;color:var(--white);border-left:1px solid #555;padding-left:6px;white-space:nowrap}
  .letterhead .offices i,.letterhead .bank i{display:inline-block;width:4px;height:4px;background:var(--yellow);border-radius:1px;margin-right:3px;vertical-align:-0.5px}
  .letterhead .footer .brand{position:absolute;left:216px;top:14px;font-size:12px}

  /* Umschlag */
  .envelope{left:380px;top:706px;width:358px;height:179px;background:var(--paper)}
  .envelope .flap{position:absolute;left:0;top:0}
  .envelope .brand{position:absolute;left:0;right:0;top:17px;justify-content:center;font-size:12px}

  /* Kurzmitteilung */
  .compliment{left:789px;top:213px;width:357px;height:180px;background:var(--ink)}
  .compliment .brand{position:absolute;left:31px;top:46px;font-size:13px}
  .compliment .address{position:absolute;left:26px;top:109px;font-size:4.8px;line-height:6.4px;font-weight:600;color:var(--white)}
  .compliment .rule{position:absolute;left:26px;top:125px;width:65px;height:1px;background:var(--yellow)}
  .compliment .contact{position:absolute;left:26px;top:129px;font-size:4.8px;line-height:6.6px;font-weight:600;color:var(--white)}
  .compliment .deco{position:absolute;left:245px;top:22px}

  /* Mappe */
  .folder{left:796px;top:417px;width:356px;height:471px;background:var(--ink);display:flex;align-items:center;justify-content:center}
  .folder .brand{font-size:22px}
</style>
</head>
<body>
<main class="canvas">

  <section class="piece card-front" aria-label="Visitenkarte Vorderseite">
    <div class="brand"><span class="dot"></span>RVB</div>
    <p class="name">LENNO <span>BRÜCHERT</span></p>
    <div class="rule"></div>
    <p class="role">Inhaber</p>
    <p class="contact"><i></i>07412-6640285<br><i></i>info@rvb-stromtechnik.de</p>
    <p class="web">www.rvb-stromtechnik.de</p>
  </section>

  <section class="piece card-back" aria-label="Visitenkarte Rückseite">
    <div class="brand"><span class="dot"></span>RVB Stromtechnik</div>
  </section>

  <section class="piece letterhead" aria-label="Briefbogen">
    <div class="brand"><span class="dot"></span>RVB</div>
    <p class="address">Im Haselgrund 9,<br>88682 Salem</p>
    <div class="rule"></div>
    <p class="mail">info@rvb-stromtechnik.de<br>www.rvb-stromtechnik.de</p>
    <svg class="deco" width="170" height="170" viewBox="0 0 170 170" aria-hidden="true">
      <circle cx="85" cy="85" r="72" fill="none" stroke="var(--faint)" stroke-width="18"/>
    </svg>
    <div class="footer">
      <svg width="317" height="44" viewBox="0 0 317 44" aria-hidden="true">
        <polygon points="0,0 198,0 217,36 0,36" fill="var(--ink)"/>
        <polygon points="276,0 317,0 317,36 300,36" fill="var(--yellow)"/>
        <rect x="0" y="40" width="317" height="2" fill="var(--yellow)"/>
      </svg>
      <p class="offices"><i></i>Tel.: 07412-6640285<br><i></i>USt.-ID: DE574016328<br><i></i>Steuer Nr.: 4190357762<br><i></i>Finanzamt Dornhalden</p>
      <p class="bank"><i></i>Kreisbank Talgau<br><i></i>IBAN: DE71480392610007315946<br><i></i>BIC: KRTAGES1XYZ</p>
      <div class="brand brand--dark">RVB</div>
    </div>
  </section>

  <section class="piece envelope" aria-label="Briefumschlag">
    <svg class="flap" width="358" height="50" viewBox="0 0 358 50" aria-hidden="true">
      <path d="M0,0 H358 L350,38 Q348,48 336,48 H22 Q10,48 8,38 Z" fill="var(--ink)"/>
    </svg>
    <div class="brand"><span class="dot"></span>RVB</div>
  </section>

  <section class="piece compliment" aria-label="Kurzmitteilung">
    <div class="brand"><span class="dot"></span>RVB</div>
    <p class="address">Im Haselgrund 9<br>88682 Salem</p>
    <div class="rule"></div>
    <p class="contact">Tel: 07412-6640285<br>Email: info@rvb-stromtechnik.de<br>Website: www.rvb-stromtechnik.de</p>
    <svg class="deco" width="110" height="110" viewBox="0 0 110 110" aria-hidden="true">
      <circle cx="55" cy="55" r="46" fill="none" stroke="#1e1e1a" stroke-width="14"/>
    </svg>
  </section>

  <section class="piece folder" aria-label="Präsentationsmappe">
    <div class="brand"><span class="dot"></span>RVB Stromtechnik</div>
  </section>

</main>
</body>
</html>
```